Weightloss company needs Business Card

We want a business card that is clean and professional, yet portrays that we are a friendly, innovative, and versatile program designed to fit the needs of our clients.
I would like there to be 2 sides, one side having an appointment card, and the other side containing the logo and business information. There can be decorations on both sides. The logo is attached.

Target Market(s)

Men and women 40-60

Industry/Entity Type

Business

Contact Information for Business Card

Font styles to use
Sans Serif

Requirements
Must have
• The logo, space for business information
Nice to have
• The colors in the logo
Should not have
• No pictures of people or food

```html
<!DOCTYPE html>
<html lang="en">
<head>
<meta charset="utf-8">
<title>Brightpath Wellness – Business Card</title>
<link href="https://fonts.googleapis.com/css2?family=Arimo:wght@400;700&display=swap" rel="stylesheet">
<style>
  :root {
    --paper-light: #ffffff;
    --paper-tint: #eef8fb;
    --brand-red: #ee1742;
    --brand-cyan: #26d9f8;
    --icon-cyan: #2bc3ef;
    --ink: #111111;
  }
  html, body {
    margin: 0;
    padding: 0;
    width: 1200px;
    height: 600px;
    overflow: hidden;
  }
  .card {
    position: relative;
    width: 1200px;
    height: 600px;
    overflow: hidden;
    background: linear-gradient(160deg, var(--paper-light) 0%, var(--paper-tint) 100%);
    font-family: "Arimo", Arial, sans-serif;
  }
  .hourglass-band {
    position: absolute;
    left: 0;
    top: 0;
  }
  .brand-name {
    position: absolute;
    left: 30px;
    top: 276px;
    width: 460px;
    margin: 0;
    text-align: center;
    font-size: 42px;
    font-weight: 700;
    color: var(--brand-red);
    letter-spacing: 0.5px;
  }
  .identity {
    position: absolute;
    right: 80px;
    top: 72px;
    text-align: right;
  }
  .person-name {
    margin: 0;
    font-size: 72px;
    font-weight: 400;
    line-height: 1;
    color: var(--brand-red);
  }
  .person-role {
    margin: 8px 0 0;
    font-size: 35px;
    font-weight: 400;
    line-height: 1.1;
    color: var(--ink);
  }
  .contact-list {
    position: absolute;
    right: 80px;
    top: 232px;
    margin: 0;
    padding: 0;
    list-style: none;
  }
  .contact-item {
    display: flex;
    justify-content: flex-end;
    align-items: center;
    gap: 14px;
    height: 36px;
    font-size: 25px;
    color: var(--brand-red);
  }
  .contact-icon {
    width: 26px;
    height: 26px;
    flex: none;
  }
  .postal-address {
    position: absolute;
    right: 80px;
    top: 370px;
    margin: 0;
    text-align: right;
    font-style: normal;
    font-size: 25px;
    line-height: 36px;
    color: var(--brand-red);
  }
</style>
</head>
<body>
<main class="card">
  <svg class="hourglass-band" width="1200" height="600" viewBox="0 0 1200 600" aria-hidden="true">
    <defs>
      <filter id="band-shadow" x="-20%" y="-5%" width="140%" height="110%">
        <feDropShadow dx="0" dy="0" stdDeviation="6" flood-color="#000" flood-opacity="0.35"/>
      </filter>
    </defs>
    <polygon points="472,0 694,0 617,300 694,600 472,600 546,300"
             fill="var(--brand-cyan)" filter="url(#band-shadow)"/>
  </svg>

  <p class="brand-name">Brightpath Wellness</p>

  <header class="identity">
    <h1 class="person-name">Daniel Hart</h1>
    <p class="person-role">Managing Director</p>
  </header>

  <ul class="contact-list">
    <li class="contact-item">
      <span>(42) 1600 555 018</span>
      <svg class="contact-icon" viewBox="0 0 26 26" aria-label="Phone">
        <rect x="8" y="2" width="11" height="21" rx="2.5" fill="none" stroke="var(--icon-cyan)" stroke-width="2.2"/>
        <rect x="10" y="5" width="7" height="12" fill="var(--icon-cyan)"/>
      </svg>
    </li>
    <li class="contact-item">
      <span>info@brightpathwell.com</span>
      <svg class="contact-icon" viewBox="0 0 26 26" aria-label="Email">
        <rect x="2" y="5" width="22" height="16" fill="var(--icon-cyan)"/>
        <polyline points="2,5 13,14 24,5" fill="none" stroke="#ffffff" stroke-width="1.6"/>
      </svg>
    </li>
    <li class="contact-item">
      <span>www.brightpathwell.com</span>
      <svg class="contact-icon" viewBox="0 0 26 26" aria-label="Website">
        <g fill="none" stroke="var(--icon-cyan)" stroke-width="1.5">
          <circle cx="13" cy="13" r="9"/>
          <ellipse cx="13" cy="13" rx="4" ry="9"/>
          <line x1="4" y1="13" x2="22" y2="13"/>
          <line x1="6" y1="8" x2="20" y2="8"/>
          <line x1="6" y1="18" x2="20" y2="18"/>
        </g>
      </svg>
    </li>
  </ul>

  <address class="postal-address">
    Postal Address number<br>
    CITY/ZIP
  </address>
</main>
</body>
</html>
```